New plumbing company requires flyer to attract new clients

We need a flyer to promote our new plumbing business so that we can attract more customers. Our plumbing business "Brenvale Plumbing and Gas" is family owned and operated and we would like to advertise that we are local to the Adelaide Hills. Our company moto is great service, quality workmanship and fair pricing. We would like to offer a 10% discount if clients like us on facebook. The flyer will be distributed by a letter box drop so it needs to be suitable for the post. We would love to encourage people to refer our company to their friends/family so we could offer more incentives for referrals. The design should be in the same style/colour scheme as our logo and website: www.brenvaleplumbingandgas.com.au

```html
<!DOCTYPE html>
<html lang="en">
<head>
<meta charset="utf-8">
<title>Brenvale Plumbing and Gas – Postcard Flyer</title>
<link rel="stylesheet" href="https://fonts.googleapis.com/css2?family=Cedarville+Cursive&family=Mulish:wght@400;700&display=swap">
<style>
  :root {
    --backdrop: #ececec;
    --card: #ffffff;
    --ink: #4a4a4a;
    --script-ink: #2e2e2e;
    --divider: #a9a9a9;
    --faint: #ededed;
    --stamp: #d6d6d6;
    --shadow: rgba(0,0,0,0.28);
  }
  * { margin: 0; padding: 0; box-sizing: border-box; }
  html, body { width: 1200px; height: 900px; overflow: hidden; background: var(--backdrop); }
  .canvas { position: relative; width: 1200px; height: 900px; font-family: "Mulish", sans-serif; color: var(--ink); }

  .card {
    position: absolute; top: 25px; height: 807px; background: var(--card);
    box-shadow: 4px 5px 6px var(--shadow);
  }
  .card--message { left: 28px; width: 572px; }
  .card--address { left: 603px; width: 569px; }
  .fold { position: absolute; left: 599px; top: 25px; width: 4px; height: 807px; background: var(--divider); }

  .brand-ghost {
    position: absolute; left: 60px; top: 265px; color: var(--faint);
    font-family: "Mulish", sans-serif; font-weight: 700; line-height: 1;
  }
  .brand-ghost__name { display: block; font-size: 64px; letter-spacing: 1px; }
  .brand-ghost__trade { display: block; font-size: 32px; margin: 4px 0 0 110px; }

  .letter {
    position: absolute; left: 47px; top: 95px; width: 470px;
    font-family: "Cedarville Cursive", cursive; font-size: 17px; color: var(--script-ink);
  }
  .letter__line { display: block; height: 41.5px; line-height: 41.5px; white-space: nowrap; }
  .letter__greeting { margin-bottom: 5px; }
  .letter__signoff { margin-top: 38px; }
  .letter__signature { line-height: 44px; }

  .return-address { position: absolute; left: 47px; top: 685px; }
  .return-address__label { font-weight: 700; font-size: 21px; display: block; line-height: 26px; }
  .return-address__place { font-size: 22px; display: block; line-height: 28px; }

  .stamp {
    position: absolute; left: 322px; top: 63px; width: 180px; height: 180px;
    border: 6px solid var(--stamp);
    display: flex; flex-direction: column; align-items: center; justify-content: center;
    color: var(--stamp); font-weight: 700; text-align: center;
  }
  .stamp__name { font-size: 36px; line-height: 1; }
  .stamp__trade { font-size: 14px; margin-top: 6px; }

  .services { position: absolute; left: 56px; top: 292px; }
  .services__title { font-weight: 700; font-size: 19px; line-height: 24px; }
  .services__list { list-style: none; font-size: 20.5px; line-height: 24.6px; }
  .services__list li::before { content: "\2022"; margin-right: 8px; }
</style>
</head>
<body>
<div class="canvas">
  <section class="card card--message">
    <div class="brand-ghost" aria-hidden="true">
      <span class="brand-ghost__name">Brenvale</span>
      <span class="brand-ghost__trade">Plumbing and Gas</span>
    </div>
    <p class="letter">
      <span class="letter__line letter__greeting">Hi,</span>
      <span class="letter__line">Brenvale Plumbing and Gas is a new family business based</span>
      <span class="letter__line">in Kestrel Vale in the Adelaide Hills. We can offer all areas of</span>
      <span class="letter__line">plumbing and gas maintenance and we are equipped with</span>
      <span class="letter__line">drain cleaning equipment and pipe cameras to get your leaks</span>
      <span class="letter__line">and blockages cleared quickly. We are keen to prove that we</span>
      <span class="letter__line">offer great service, quality workmanship and fair pricing so</span>
      <span class="letter__line">when your next plumbing problem arises think of Brenvale</span>
      <span class="letter__line">Plumbing and Gas.</span>
      <span class="letter__line letter__signoff">Cheers,</span>
      <span class="letter__line letter__signature">Tom Hadley (Owner)</span>
    </p>
    <div class="return-address">
      <span class="return-address__label">Return Address:</span>
      <span class="return-address__place">Kestrel Vale, South Australia 5150</span>
    </div>
  </section>

  <div class="fold"></div>

  <section class="card card--address">
    <div class="stamp">
      <span class="stamp__name">Brenvale</span>
      <span class="stamp__trade">Plumbing and Gas</span>
    </div>
    <div class="services">
      <h2 class="services__title">Services Include:</h2>
      <ul class="services__list">
        <li>24/7 Emergency Plumbing</li>
        <li>Pipe, Tap, Shower &amp; Toilet Repairs</li>
        <li>Blocked Drains</li>
        <li>Stormwater &amp; Sewer</li>
        <li>Hot Water Repairs &amp; Installation</li>
        <li>Internal Pipe Inspections</li>
        <li>Backflow Prevention &amp; Testing</li>
        <li>Renovations</li>
        <li>Gas Connections and Appliance Servicing</li>
        <li>Blocked Drains</li>
        <li>Leak Detection</li>
        <li>Pressure Testing</li>
        <li>Rainwater Tank Repairs and Installation</li>
        <li>Water Filters</li>
      </ul>
    </div>
  </section>
</div>
</body>
</html>
```